Harborline Auto LLC

Car Dealer Customer Service
Address: 2874 Cresthaven Road, Shelbyville, TN 37162
web: www.harborlineautoxq.net
email: harborlineautoxq@mailnest.example
Phone: (931) 555-0148
Phone: (629) 555-0173

```html
<!DOCTYPE html>
<html lang="en">
<head>
<meta charset="utf-8">
<title>Harborline Auto – Business Card</title>
<link href="https://fonts.googleapis.com/css2?family=Montserrat:wght@400;500;800&display=swap" rel="stylesheet">
<style>
  :root {
    --brand-blue: #1b7aab;
    --accent-gold: #eeb140;
    --ink: #1d1d1d;
    --paper: #ffffff;
    --backdrop: #2b2b2b;
  }
  * { margin: 0; padding: 0; box-sizing: border-box; }
  html, body { width: 1200px; height: 960px; overflow: hidden; background: var(--backdrop); }
  body { font-family: "Montserrat", sans-serif; position: relative; }

  .card {
    position: absolute;
    left: 250px;
    width: 700px;
    height: 400px;
    border-radius: 26px;
    overflow: hidden;
  }
  .card--front { top: 60px; background: var(--brand-blue); }
  .card--back { top: 500px; background: var(--paper); }

  .brand {
    position: absolute;
    display: flex;
    align-items: center;
    font-weight: 800;
    letter-spacing: 1px;
    text-transform: uppercase;
    white-space: nowrap;
  }
  .brand__dot { border-radius: 50%; flex: none; }

  .card--front .brand {
    left: 50%; top: 50%;
    transform: translate(-50%, -50%);
    gap: 18px;
    font-size: 46px;
    color: var(--paper);
  }
  .card--front .brand__dot { width: 54px; height: 54px; background: var(--paper); }

  .card--back .brand {
    left: 36px; top: 128px;
    gap: 12px;
    font-size: 21px;
    color: var(--brand-blue);
  }
  .card--back .brand__dot { width: 28px; height: 28px; background: var(--brand-blue); }

  .divider {
    position: absolute;
    left: 338px; top: 48px;
    width: 2px; height: 180px;
    background: var(--brand-blue);
  }

  .contact {
    position: absolute;
    left: 358px; top: 46px;
    font-size: 13.5px;
    line-height: 1.5;
    color: var(--ink);
    list-style: none;
  }
  .contact__row { display: flex; align-items: center; gap: 9px; }
  .contact__icon { width: 14px; height: 14px; flex: none; fill: var(--brand-blue); }
  .contact__icon--line { fill: none; stroke: var(--brand-blue); stroke-width: 2.4; }
  .contact__web-name { color: var(--brand-blue); }
  .contact__address { margin-bottom: 4px; }

  .wave { position: absolute; left: 0; bottom: 0; width: 700px; height: 170px; }
</style>
</head>
<body>

  <section class="card card--front" aria-label="Card front">
    <div class="brand"><span class="brand__dot"></span>Harborline Auto</div>
  </section>

  <section class="card card--back" aria-label="Card back">
    <div class="brand"><span class="brand__dot"></span>Harborline Auto</div>

    <div class="divider"></div>

    <ul class="contact">
      <li class="contact__title">Car Dealer Customer Service</li>
      <li class="contact__address">2874 Cresthaven Road,<br>Shelbyville, TN 37162</li>
      <li class="contact__row">
        <svg class="contact__icon" viewBox="0 0 24 24" aria-hidden="true"><path d="M6.6 10.8a15.1 15.1 0 0 0 6.6 6.6l2.2-2.2a1 1 0 0 1 1-.25 11.4 11.4 0 0 0 3.6.57 1 1 0 0 1 1 1V20a1 1 0 0 1-1 1A17 17 0 0 1 3 4a1 1 0 0 1 1-1h3.5a1 1 0 0 1 1 1c0 1.25.2 2.45.57 3.57a1 1 0 0 1-.25 1z"/></svg>
        (931) 555-0148
      </li>
      <li class="contact__row">
        <svg class="contact__icon" viewBox="0 0 24 24" aria-hidden="true"><path d="M2 9c4-4 16-4 20 0v3h-5V10c-3-1-7-1-10 0v2H2z"/><path d="M6 13h12l2 7H4z"/></svg>
        (629) 555-0173
      </li>
      <li class="contact__row">
        <svg class="contact__icon contact__icon--line" viewBox="0 0 24 24" aria-hidden="true"><path d="M3 5h18v14H3z M3 5l9 8 9-8"/></svg>
        harborlineautoxq@mailnest.example
      </li>
      <li class="contact__row">
        <svg class="contact__icon" viewBox="0 0 24 24" aria-hidden="true"><circle cx="12" cy="12" r="10"/></svg>
        <span>www.<span class="contact__web-name">harborlineautoxq</span>.net</span>
      </li>
    </ul>

    <svg class="wave" viewBox="0 0 700 170" preserveAspectRatio="none" aria-hidden="true">
      <path d="M0 160 C 220 152, 340 110, 470 55 C 560 18, 640 6, 700 6 L700 170 L0 170 Z" fill="var(--accent-gold)"/>
      <path d="M0 166 C 220 158, 345 118, 478 63 C 568 26, 645 14, 700 14 L700 170 L0 170 Z" fill="var(--paper)"/>
      <path d="M0 170 C 230 164, 352 126, 486 71 C 576 34, 650 22, 700 22 L700 170 Z" fill="var(--brand-blue)"/>
    </svg>
  </section>

</body>
</html>
```